Creation of an elegant and modern turnkey Shopify website

Hello,

We are a new company specializing in the sale of above-ground pools. We want to create a turnkey website, ideally using Shopify. For now, we need a "showcase" site, not an e-commerce platform, with four tabs:

Home Page (an overall presentation of the company)
Our Products (an overview of all the above-ground pools we sell)
Our Projects (a page inspired by Instagram to showcase photos of our future projects)
Contact (a page with all our contact information and a contact form)

We are looking to create a highly visual, elegant, and modern website with vibrant splashes of color. We will provide the text, photos (along with instructions on where to place them on each page), and all other necessary information as attachments.

Thank you in advance for your proposals!

The Brisa Lagoon Team

Target Market(s)

Targeted at Swiss customers (a translator will need to be installed for different languages)

Industry/Entity Type

Sale of customised above-ground pools

Coding

Coded - Design and coding required

Font styles to use
Sans Serif

Colors
0094D4
00A9DD
6FCCEA
C7EBF8
E9F6FB
00AB8E
00BBA5
67D7C9
C6EFE9
E9F9F6

Requirements
Must have
• A stunning, elegant and modern look
Nice to have
• Inspiration from the colors of our logo throughout the site, but in an elegant way
Should not have
• An overly classic look for swimming pool sites

```html
<!DOCTYPE html>
<html lang="en">
<head>
<meta charset="utf-8">
<title>Brisa Lagoon — Above-Ground Pools</title>
<link href="https://fonts.googleapis.com/css2?family=Josefin+Sans:wght@300;400&family=Montserrat:wght@400;500&display=swap" rel="stylesheet">
<style>
:root{
  --mint:#67D7C9;
  --mint-soft:#6BD8C9;
  --sky:#7CCFE6;
  --aqua:#00A9DD;
  --ink:#111;
  --text:#333;
  --muted:#f4f4f4;
  --line:#e6e6e6;
  --white:#fff;
  --black:#000;
}
*{box-sizing:border-box;margin:0;padding:0}
html,body{width:1200px;height:3639px;overflow:hidden}
body{position:relative;font-family:"Montserrat",sans-serif;color:var(--text);background:var(--white)}
.abs{position:absolute}
.head{font-family:"Josefin Sans",sans-serif;font-weight:300;color:var(--ink);text-transform:uppercase;letter-spacing:.5px}
.btn{position:absolute;display:flex;align-items:center;justify-content:center;background:var(--mint);color:#0f3b38;font-family:"Josefin Sans",sans-serif;font-size:15px;text-transform:uppercase}
.center{left:0;width:1200px;text-align:center}

.promo-bar{top:0;left:0;width:1200px;height:38px;background:var(--mint-soft);font-size:12px;font-weight:500;color:#123;display:flex;align-items:center;justify-content:center}
.contact-row{top:38px;left:0;width:1200px;height:51px;border-bottom:1px solid var(--line);font-size:12px;color:#222}
.contact-row .item{position:absolute;top:15px;display:flex;gap:6px;align-items:center}
.search{position:absolute;left:758px;top:9px;width:326px;height:33px;background:#f2f2f2;font-size:10px;color:#888;padding:11px 18px}
.search svg{position:absolute;right:18px;top:11px}
.nav{top:89px;left:0;width:1200px;height:82px}
.brand{position:absolute;left:127px;top:18px;font-family:"Josefin Sans",sans-serif;font-weight:300;font-size:20px;line-height:22px;color:var(--ink)}
.nav-links{position:absolute;top:34px;font-size:14px;color:#222}
.nav-icons{position:absolute;top:32px;left:1028px;display:flex;gap:18px}

.hero{top:171px;left:0;width:1200px;height:555px;background:linear-gradient(180deg,#8fb6c4 0%,#3f9fb4 45%,#2a8ea9 58%,#a97a58 75%,#6b4a33 100%)}
.hero-welcome{top:310px;font-family:"Josefin Sans",sans-serif;font-weight:300;font-size:25px;color:var(--mint)}
.hero-title{top:340px;font-family:"Josefin Sans",sans-serif;font-weight:400;font-size:104px;color:var(--white);letter-spacing:2px}
.hero-copy{top:462px;font-size:13px;line-height:21px;color:var(--white)}

.intro{top:726px;left:0;width:1200px;height:357px;background:var(--muted)}
.h-lg{font-size:38px;line-height:48px}
.tagline{top:903px;font-size:14px;color:var(--mint)}
.intro-copy{top:940px;left:190px;width:820px;font-size:12px;line-height:25px;color:#222;text-align:center}

.card-img{top:1272px;height:193px}
.card-title{top:1491px;width:316px;font-family:"Josefin Sans",sans-serif;font-size:17px;text-align:center;text-transform:uppercase;color:var(--ink)}
.card-text{top:1518px;width:316px;font-size:12px;line-height:20px;text-align:center;color:#222}
.arrow{top:1380px;width:22px;height:22px;border-radius:50%;background:#888;display:flex;align-items:center;justify-content:center}

.service{top:1656px;left:0;width:1200px;height:446px;background:var(--muted)}
.side-copy{font-size:12px;line-height:25px;color:#222}

.satisfaction{top:2102px;left:0;width:1200px;height:379px;background:var(--sky)}

.footer{top:3226px;left:0;width:1200px;height:413px;background:var(--black);color:var(--white)}
.f-head{font-family:"Josefin Sans",sans-serif;font-size:18px;text-transform:uppercase;color:var(--white)}
.f-list{font-size:14px;line-height:30px;color:var(--white)}
</style>
</head>
<body>

<div class="abs promo-bar">Free Shipping On Orders Over $200</div>

<div class="abs contact-row">
  <div class="item" style="left:127px">
    <svg width="11" height="11" viewBox="0 0 24 24"><path fill="#222" d="M6.6 10.8a15 15 0 0 0 6.6 6.6l2.2-2.2a1 1 0 0 1 1-.25 11.4 11.4 0 0 0 3.6.57 1 1 0 0 1 1 1V20a1 1 0 0 1-1 1A17 17 0 0 1 3 4a1 1 0 0 1 1-1h3.5a1 1 0 0 1 1 1c0 1.25.2 2.45.57 3.57a1 1 0 0 1-.25 1z"/></svg>
    Call : 100-555-0142</div>
  <div class="item" style="left:311px">
    <svg width="12" height="10" viewBox="0 0 24 20"><rect x="1" y="1" width="22" height="18" rx="2" fill="none" stroke="#222" stroke-width="2"/><path d="M1 2l11 9 11-9" fill="none" stroke="#222" stroke-width="2"/></svg>
    hello@brisalagoon.example</div>
  <div class="search">Search
    <svg width="10" height="10" viewBox="0 0 24 24"><circle cx="10" cy="10" r="7" fill="none" stroke="#111" stroke-width="3"/><path d="M15 15l7 7" stroke="#111" stroke-width="3"/></svg></div>
</div>

<div class="abs nav">
  <div class="brand">BRISA<br><span style="color:var(--aqua)">LAGOON</span></div>
  <div class="nav-links" style="left:405px">Home</div>
  <div class="nav-links" style="left:479px">Our Products</div>
  <div class="nav-links" style="left:603px">Our Projects</div>
  <div class="nav-links" style="left:720px">Contact Us</div>
  <div class="nav-icons">
    <svg width="16" height="16" viewBox="0 0 24 24"><circle cx="12" cy="7" r="5" fill="#111"/><path d="M3 23c0-6 4-9 9-9s9 3 9 9z" fill="#111"/></svg>
    <svg width="18" height="16" viewBox="0 0 24 20"><path d="M2 7h20l-3 12H5z" fill="none" stroke="var(--aqua)" stroke-width="2"/><path d="M7 7l5-6 5 6" fill="none" stroke="var(--aqua)" stroke-width="2"/></svg>
  </div>
</div>

<div class="abs hero" role="img" aria-label="Pool edge seen from a wooden deck, palm and terrace blurred behind"></div>
<div class="abs center hero-welcome">WELCOME TO</div>
<div class="abs center hero-title">BRISA LAGOON</div>
<div class="abs center hero-copy">Lorem ipsum dolor sit amet, consectetur adipiscing elit, sed do eiusmod<br>tempor incididunt ut labore et dolore magna aliqua.</div>
<div class="btn" style="left:510px;top:522px;width:128px;height:45px">Shop Now</div>

<section class="abs intro"></section>
<h1 class="abs center head h-lg" style="top:792px">Transform your garden with<br>our premium above-ground pools!</h1>
<div class="abs center tagline">Achieve your dreams with our custom, tailor-made above-ground pools.</div>
<p class="abs intro-copy">Imagine an exceptional relaxation and leisure space right in your own backyard. With our unparalleled expertise and commitment to excellence, we create above-ground pools that exceed all expectations. Our exclusive, custom-designed models are crafted to combine style, durability, and innovation, offering a unique and refined experience.</p>

<h2 class="abs center head h-lg" style="top:1148px;line-height:42px">Why choose our<br>above-ground pools?</h2>
<div class="arrow abs" style="left:51px"><svg width="8" height="10" viewBox="0 0 8 10"><path d="M6 1L2 5l4 4" fill="none" stroke="#fff" stroke-width="2"/></svg></div>
<div class="arrow abs" style="left:1129px"><svg width="8" height="10" viewBox="0 0 8 10"><path d="M2 1l4 4-4 4" fill="none" stroke="#fff" stroke-width="2"/></svg></div>

<div class="abs card-img" style="left:112px;width:316px;background:linear-gradient(135deg,#2f8fcf,#6fd0ef 60%,#3b7c46)" role="img" aria-label="Overhead view of a blue tiled pool framed by greenery"></div>
<div class="abs card-img" style="left:442px;width:316px;background:linear-gradient(180deg,#7fb6e4 0%,#e9d2b0 45%,#2b8fb7 80%,#6d5a48)" role="img" aria-label="Modern villa with loungers beside a lit pool"></div>
<div class="abs card-img" style="left:773px;width:317px;background:linear-gradient(180deg,#4e8ed8 0%,#c9def0 40%,#2f6ea6 70%,#8fa5b0)" role="img" aria-label="Glass house with an infinity pool overlooking the sea"></div>

<div class="abs card-title" style="left:112px">Superior quality:</div>
<div class="abs card-text" style="left:112px">Each pool is constructed with high-quality<br>materials, ensuring exceptional<br>durability and strength.</div>
<div class="abs card-title" style="left:442px">Elegant design:</div>
<div class="abs card-text" style="left:442px">Our pools come in a variety of styles and<br>finishes,seamlessly blending into<br>any garden setting.</div>
<div class="abs card-title" style="left:773px">Custom and tailor-made:</div>
<div class="abs card-text" style="left:773px">Create the pool of your dreams with our<br>customization options, tailored to your<br>specific tastes and needs.</div>

<section class="abs service"></section>
<div class="abs" style="top:1656px;left:0;width:599px;height:446px;background:linear-gradient(135deg,#9fe0ea,#d9f3f5 45%,#c99b82 60%,#58bfcf)" role="img" aria-label="Swimmer's legs resting at the edge of a sparkling pool, wide hat in the foreground"></div>
<h2 class="abs head h-lg" style="top:1755px;left:631px">Personalized services</h2>
<p class="abs side-copy" style="top:1813px;left:631px;width:460px">We understand that every garden and client is unique. That's why we offer personalized services, from design to installation and after-sales support. Our team of experts is here to answer all your questions and guide you throughout your project.</p>
<div class="btn" style="left:630px;top:1937px;width:128px;height:45px">Learn More</div>

<section class="abs satisfaction" role="img" aria-label="Soft rippling pool water backdrop"></section>
<h2 class="abs center head h-lg" style="top:2180px">Guaranteed satisfaction</h2>
<p class="abs" style="top:2246px;left:170px;width:860px;text-align:center;font-size:16px;line-height:30px;color:#1d2b30">Your satisfaction is our top priority. We are committed to providing you with exceptional service and the high-est quality products. Join our community of satisfied customers who are already enjoying their custom above-ground pools. 10-Year Warranty!</p>
<div class="btn" style="left:512px;top:2358px;width:130px;height:45px;background:var(--white)">Learn More</div>

<h2 class="abs head h-lg" style="top:2650px;left:110px">Contact us today</h2>
<p class="abs side-copy" style="top:2710px;left:110px;width:430px">Don't wait any longer to transform your garden into a wellness oasis. Contact us today to discover our range of customizable above-ground pools and get a tailored quote. Dive into a world of infinite possibilities with [Your Company Name].</p>
<div class="btn" style="left:109px;top:2833px;width:127px;height:46px">Learn More</div>
<div class="abs" style="top:2561px;left:603px;width:487px;height:381px;background:linear-gradient(135deg,#8ecbe6 0%,#5cc2b4 40%,#e8f1ef 65%,#2a8c6f 100%)" role="img" aria-label="Striped teal and white beach cabin with towels hanging"></div>

<section class="abs" style="top:3025px;left:0;width:1200px;height:201px;background:var(--muted)"></section>
<h2 class="abs center head h-lg" style="top:3098px">We bring your pool dreams to life!</h2>
<div class="abs" style="top:3158px;left:335px;width:770px;height:52px;background:linear-gradient(90deg,rgba(159,232,240,0),rgba(159,232,240,.7) 55%,rgba(159,232,240,0))" role="img" aria-label="Line drawing of a pool with a lounge chair beside it"></div>

<footer class="abs footer">
  <div class="abs" style="left:152px;top:76px;font-family:'Josefin Sans',sans-serif;font-weight:300;font-size:56px;line-height:64px;color:var(--white)">BRISA<br><span style="color:var(--aqua)">LAGOON</span></div>
  <div class="abs" style="left:190px;top:247px;display:flex;gap:6px">
    <span style="width:20px;height:20px;border-radius:50%;background:var(--white)"></span>
    <span style="width:20px;height:20px;border-radius:50%;background:var(--white)"></span>
    <span style="width:20px;height:20px;border-radius:50%;background:var(--white)"></span>
    <span style="width:20px;height:20px;border-radius:50%;background:var(--white)"></span>
  </div>

  <div class="abs f-head" style="left:449px;top:80px">Contact Information</div>
  <div class="abs f-list" style="left:449px;top:120px;line-height:22px">
    <div style="display:flex;gap:14px"><svg width="12" height="16" viewBox="0 0 12 16" style="margin-top:3px"><path d="M6 0a6 6 0 0 1 6 6c0 4-6 10-6 10S0 10 0 6a6 6 0 0 1 6-6z" fill="#fff"/><circle cx="6" cy="6" r="2" fill="#000"/></svg><span>12b Brisa Lagoon dolor sit amet,<br>consectetur adipiscing elit,</span></div>
    <div style="display:flex;gap:14px;margin-top:18px;align-items:center"><svg width="14" height="11" viewBox="0 0 24 20"><rect width="24" height="20" rx="2" fill="#fff"/><path d="M1 2l11 9 11-9" fill="none" stroke="#000" stroke-width="2"/></svg>hello@brisalagoon.example</div>
    <div style="display:flex;gap:14px;margin-top:14px;align-items:center"><svg width="13" height="13" viewBox="0 0 24 24"><path fill="#fff" d="M6.6 10.8a15 15 0 0 0 6.6 6.6l2.2-2.2a1 1 0 0 1 1-.25 11.4 11.4 0 0 0 3.6.57 1 1 0 0 1 1 1V20a1 1 0 0 1-1 1A17 17 0 0 1 3 4a1 1 0 0 1 1-1h3.5a1 1 0 0 1 1 1c0 1.25.2 2.45.57 3.57a1 1 0 0 1-.25 1z"/></svg>100-555-0142</div>
  </div>

  <div class="abs f-head" style="left:772px;top:82px">Quick Links</div>
  <div class="abs f-list" style="left:777px;top:120px">Home<br>Our Products<br>Our Projects<br>Contact Us</div>
  <div class="abs f-head" style="left:950px;top:82px">Support</div>
  <div class="abs f-list" style="left:950px;top:120px">Terms&amp;condtions<br>Privacy Policy<br>Terms of Use</div>

  <div class="abs" style="left:112px;top:315px;width:976px;height:1px;background:#333"></div>
  <div class="abs center" style="top:350px;font-size:15px">©Copyrights 2024 Brisa Lagoon. &nbsp;| &nbsp;&nbsp;All Rights Reserved</div>
</footer>

</body>
</html>
```